Business Card Design

We provide services doing multiple jobs in the construction industry.Please note: The company name needs to be ROCK SOLID BUILDING SERVICESAttached logo was an example of what we wanted. Can you change up the colors?

Industry/Entity Type

Construction

Contact Information for Business Card

ROCK SOLID BUILDING SERVICES5401 HUDSON BEND RDAUSTIN, TX 78734(512)243-6854ROCKSOLIDBUILDINGSERVICES@GMAIL.COM

```html
<!DOCTYPE html>
<html lang="en">
<head>
<meta charset="utf-8">
<title>Pearlwood Framing Works – Business Card</title>
<link rel="stylesheet" href="https://fonts.googleapis.com/css2?family=Anton&family=Roboto:wght@400;700&display=swap">
<style>
  :root {
    --ink: #0a0607;
    --paper: #ffffff;
    --paper-shade: #ececee;
    --steel: #5c7d8f;
    --navy: #1f2f6b;
    --stage: #e4e4e2;
    --display: "Anton", "Impact", sans-serif;
    --body: "Roboto", "Arial", sans-serif;
  }
  * { box-sizing: border-box; margin: 0; padding: 0; }
  html, body { width: 1200px; height: 800px; overflow: hidden; }
  body {
    background: var(--stage);
    display: flex;
    flex-direction: column;
    align-items: center;
    justify-content: center;
    gap: 28px;
    font-family: var(--body);
  }
  .card {
    position: relative;
    width: 630px;
    height: 360px;
    background: var(--ink);
    overflow: hidden;
    box-shadow: 0 6px 18px rgba(0,0,0,.18);
  }
  .card__shape { position: absolute; inset: 0; width: 100%; height: 100%; }
  .brand {
    position: absolute;
    left: 34px;
    bottom: 40px;
    color: var(--paper);
    line-height: 1;
  }
  .brand__name {
    font-family: var(--display);
    font-size: 42px;
    letter-spacing: .5px;
    display: block;
  }
  .brand__tagline {
    font-family: var(--body);
    font-size: 15px;
    letter-spacing: .5px;
    display: block;
    margin-top: 4px;
  }
  .mark {
    position: absolute;
    right: 34px;
    top: 84px;
    display: flex;
    align-items: center;
    gap: 12px;
    color: var(--navy);
    font-family: var(--body);
    font-weight: 700;
    font-size: 22px;
    line-height: 1.1;
  }
  .mark__square { width: 28px; height: 28px; background: var(--navy); flex: none; }
  .contact {
    position: absolute;
    right: 26px;
    top: 206px;
    color: var(--ink);
    font-size: 12px;
    font-style: normal;
    line-height: 1.7;
    text-align: right;
    text-transform: uppercase;
    white-space: nowrap;
  }
</style>
</head>
<body>

  <section class="card card--back" aria-label="Business card back">
    <svg class="card__shape" viewBox="0 0 630 360" aria-hidden="true">
      <circle cx="685" cy="330" r="432" fill="var(--steel)"/>
      <circle cx="710" cy="320" r="420" fill="var(--paper-shade)"/>
    </svg>
    <div class="brand">
      <span class="brand__name">PEARLWOOD</span>
      <span class="brand__tagline">FRAMING WORKS</span>
    </div>
  </section>

  <section class="card card--front" aria-label="Business card front">
    <svg class="card__shape" viewBox="0 0 630 360" aria-hidden="true">
      <circle cx="685" cy="330" r="432" fill="var(--steel)"/>
      <circle cx="710" cy="320" r="420" fill="var(--paper)"/>
    </svg>
    <div class="brand">
      <span class="brand__name">PEARLWOOD</span>
      <span class="brand__tagline">FRAMING WORKS</span>
    </div>
    <div class="mark">
      <span class="mark__square"></span>
      <span class="mark__name">PEARLWOOD<br>FRAMING WORKS</span>
    </div>
    <address class="contact">
      <div class="contact__phone">(512)555-0193</div>
      <div class="contact__street">7732 FERNGLEN PASS LN AUSTIN, TX 78734</div>
      <div class="contact__email">PEARLWOODFRAMINGWORKS@MAILNEST.EXAMPLE</div>
    </address>
  </section>

</body>
</html>
```